Book cover

I am working with my publisher to publish my book They came up with a book cover but I don't like it. I want to see different designs. The book Title is Brightwater the subtitle Ways to Guide Teams Through Storms with Poise, Purpose & Pace by Marlene T. Ostrowski
I want to use my Brand Colors including the blue. I am uploading the covers of my other book. This is a professional leadership book. The publisher will make the cover when providing them a new design. the Brightwater one is one I played with on Canva. I would like more color and to incorporate the blue. I want a spot at the top where I can write a quote. Brightwater is one word in the text so should be the same on the cover. I want the cover to show energy movement and am open to an image too. I am attaching logos for the feel of the brand and brand rgb codes.

```html
<!DOCTYPE html>
<html lang="en">
<head>
<meta charset="utf-8">
<title>Brightwater — Book Cover</title>
<link rel="stylesheet" href="https://fonts.googleapis.com/css2?family=Noto+Serif:ital,wght@0,400;0,600;0,700;1,400&display=swap">
<style>
  :root {
    --stage: #d8d7d4;
    --ember-dark: #5e0410;
    --ember: #d8141c;
    --flame: #f2441a;
    --glow-orange: #ff9a3c;
    --glow-core: #fff1d6;
    --magenta: #e2237a;
    --violet: #6a2a8c;
    --teal: #3a909f;
    --ink-light: #ffffff;
  }
  * { box-sizing: border-box; margin: 0; padding: 0; }
  html, body {
    width: 1200px;
    height: 809px;
    overflow: hidden;
    background: var(--stage);
  }
  .book-cover {
    position: absolute;
    left: 314px;
    top: 0;
    width: 572px;
    height: 809px;
    overflow: hidden;
    font-family: "Noto Serif", Georgia, serif;
    color: var(--ink-light);
  }
  .cover-art {
    position: absolute;
    inset: 0;
    background:
      radial-gradient(ellipse 22% 8% at 50% 61%, var(--glow-core) 0%, rgba(255,190,120,0.85) 40%, rgba(255,150,60,0) 100%),
      radial-gradient(ellipse 60% 14% at 50% 63%, rgba(255,160,70,0.75) 0%, rgba(236,60,110,0.55) 55%, rgba(226,35,122,0) 100%),
      radial-gradient(ellipse 12% 60% at 50% 20%, rgba(255,130,40,0.7) 0%, rgba(255,90,30,0) 100%),
      radial-gradient(ellipse 45% 30% at 22% 28%, rgba(106,42,140,0.45) 0%, rgba(106,42,140,0) 100%),
      radial-gradient(ellipse 45% 30% at 78% 28%, rgba(106,42,140,0.45) 0%, rgba(106,42,140,0) 100%),
      radial-gradient(ellipse 80% 70% at 50% 55%, var(--flame) 0%, var(--ember) 55%, var(--ember-dark) 100%);
  }
  .cover-quote {
    position: absolute;
    top: 88px;
    left: 0;
    width: 100%;
    text-align: center;
    font-weight: 600;
    font-size: 20px;
    line-height: 25px;
    text-shadow: 0 1px 3px rgba(60,0,10,0.5);
  }
  .cover-quote cite {
    display: block;
    margin-top: 7px;
    font-style: normal;
    font-size: 15.5px;
    line-height: 20px;
  }
  .cover-title {
    position: absolute;
    top: 282px;
    left: 0;
    width: 100%;
    text-align: center;
    font-weight: 700;
    font-size: 80px;
    line-height: 100px;
    letter-spacing: -1px;
    text-shadow: 0 3px 8px rgba(50,0,10,0.55);
    z-index: 2;
  }
  .subtitle-band {
    position: absolute;
    left: 57px;
    top: 374px;
    width: 460px;
    height: 102px;
    filter: drop-shadow(0 3px 6px rgba(50,0,10,0.45));
  }
  .subtitle-band polygon { fill: var(--teal); }
  .cover-subtitle {
    position: absolute;
    left: 57px;
    top: 374px;
    width: 460px;
    height: 102px;
    display: flex;
    flex-direction: column;
    justify-content: center;
    text-align: center;
    font-style: italic;
    font-weight: 400;
    font-size: 23px;
    line-height: 31px;
    text-shadow: 0 1px 2px rgba(0,40,50,0.35);
  }
  .cover-author {
    position: absolute;
    top: 752px;
    left: 0;
    width: 100%;
    text-align: center;
    font-weight: 600;
    font-size: 20px;
    line-height: 26px;
    text-shadow: 0 1px 3px rgba(60,0,10,0.5);
  }
</style>
</head>
<body>
  <main class="book-cover">
    <div class="cover-art" role="img" aria-label="Abstract radiant burst of red, orange, magenta and violet energy streams flaring from a bright central glow"></div>

    <blockquote class="cover-quote">
      <p>Brightwater is the essential playbook<br>to turn uncertainty into possibility</p>
      <cite>- Marlene T. Ostrowski</cite>
    </blockquote>

    <h1 class="cover-title">Brightwater</h1>

    <svg class="subtitle-band" viewBox="0 0 460 102" aria-hidden="true">
      <polygon points="16,0 460,0 442,102 0,102"/>
    </svg>
    <p class="cover-subtitle">
      <span>Ways to Guide Teams Through Storms</span>
      <span>with Poise, Purpose &amp; Pace</span>
    </p>

    <p class="cover-author">by Marlene T. Ostrowski</p>
  </main>
</body>
</html>
```